Whitcombe Business Card Design

The name of the business is Dario Whitcombe, CPA LLC
The service that we offer is Accounting, Tax & Consulting Services. I need it to have the following items:
Dario Whitcombe, Principal
Phone Number
Email Address
Physical Address

I have attached the company logo, one in black and one in white. Please provide a design in black background and the other in white background. Please include "Accounting, Tax & Consulting Services". I want the business card to be clean and very professional.

```html
<!DOCTYPE html>
<html lang="en">
<head>
<meta charset="utf-8">
<title>Dario Whitcombe, CPA LLC — Business Cards</title>
<link rel="stylesheet" href="https://fonts.googleapis.com/css2?family=Montserrat:wght@500;600&family=Poppins:wght@400;600&display=swap">
<style>
  :root {
    --backdrop: #2b2b2b;
    --ink-black: #0a0a0a;
    --brand-red: #9b171b;
    --paper-white: #ffffff;
    --muted-grey: #8c8c8c;
  }
  * { box-sizing: border-box; margin: 0; padding: 0; }
  html, body { width: 1200px; height: 1015px; overflow: hidden; }
  body {
    background: var(--backdrop);
    position: relative;
    font-family: "Poppins", sans-serif;
    color: var(--paper-white);
  }
  .card {
    position: absolute;
    width: 560px;
    height: 320px;
    overflow: hidden;
    box-shadow: 0 18px 40px rgba(0,0,0,.55);
  }
  .card--front { left: 110px; top: 95px; background: var(--ink-black); }
  .card--back  { left: 530px; top: 560px; background: var(--brand-red); }

  .brand {
    position: absolute;
    display: flex;
    align-items: center;
    gap: 14px;
    font-family: "Montserrat", sans-serif;
  }
  .brand__mark {
    width: 34px; height: 34px;
    background: var(--paper-white);
    flex: none;
  }
  .brand__name {
    font-weight: 600;
    font-size: 25px;
    letter-spacing: .5px;
    line-height: 1;
    color: var(--paper-white);
    white-space: nowrap;
  }
  .brand__tagline {
    font-family: "Montserrat", sans-serif;
    font-weight: 500;
    font-size: 15px;
    letter-spacing: 3px;
    margin-top: 8px;
    white-space: nowrap;
  }
  .card--front .brand { left: 0; right: 0; top: 96px; justify-content: center; }
  .card--front .brand__tagline { color: var(--muted-grey); }

  .service-band {
    position: absolute;
    left: 0; right: 0; bottom: 0;
    height: 70px;
    background: var(--brand-red);
    display: flex; align-items: center; justify-content: center;
    font-family: "Montserrat", sans-serif;
    font-weight: 500;
    font-size: 16px;
    letter-spacing: 1px;
    text-transform: uppercase;
  }

  .contact {
    position: absolute;
    left: 300px; top: 38px;
    font-size: 13px;
    line-height: 1.35;
  }
  .contact__name { font-weight: 600; font-size: 19px; line-height: 1.1; }
  .contact__role { font-size: 14px; margin-bottom: 16px; }
  .contact__row { display: flex; align-items: center; gap: 9px; }
  .contact__row svg { width: 16px; height: 16px; flex: none; }
  .contact__address { margin-top: 14px; padding-left: 25px; }

  .card--back .brand { left: 36px; top: 230px; }
  .card--back .brand__tagline { color: var(--paper-white); }
</style>
</head>
<body>

  <section class="card card--front" aria-label="Business card front">
    <div class="brand" style="flex-direction:column; gap:0;">
      <div style="display:flex; align-items:center; gap:14px;">
        <span class="brand__mark"></span>
        <span class="brand__name">DARIO WHITCOMBE, CPA, LLC</span>
      </div>
      <span class="brand__tagline">CERTIFIED PUBLIC ACCOUNTANT</span>
    </div>
    <div class="service-band">Accounting, Tax &amp; Consulting Services</div>
  </section>

  <section class="card card--back" aria-label="Business card back">
    <div class="contact">
      <p class="contact__name">Dario Whitcombe</p>
      <p class="contact__role">Principal</p>
      <p class="contact__row">
        <svg viewBox="0 0 16 16" aria-hidden="true"><rect x="1" y="1" width="14" height="14" rx="2" fill="none" stroke="#fff" stroke-width="1.4"/><path d="M5 4.5c0 4 2.5 6.5 6.5 7l.8-1.8-2-1-1 1c-1.2-.5-2-1.3-2.5-2.5l1-1-1-2z" fill="#fff"/></svg>
        <span>044-123 456 789</span>
      </p>
      <p class="contact__row">
        <svg viewBox="0 0 16 16" aria-hidden="true"><rect x="1" y="3" width="14" height="10" fill="#fff"/><path d="M1 3l7 6 7-6" fill="none" stroke="#9b171b" stroke-width="1.3"/></svg>
        <span>info@webname.com</span>
      </p>
      <p class="contact__address">421, Address line here<br>Country Name, 45452</p>
    </div>
    <div class="brand" style="flex-direction:column; align-items:flex-start; gap:0;">
      <div style="display:flex; align-items:center; gap:14px;">
        <span class="brand__mark"></span>
        <span class="brand__name">DARIO WHITCOMBE, CPA, LLC</span>
      </div>
      <span class="brand__tagline">CERTIFIED PUBLIC ACCOUNTANT</span>
    </div>
  </section>

</body>
</html>
```